Holistic Health Coach needs simple web site design for a new practice

I need a web (re)design for my entire site, Ridgeway Fern Lady. I have a beautiful new blue and green logo that I'd like the site fonts and color scheme to be built around. I'll attach my new logo so you'll know the colors/design feel I'm after.

I want easy navigation for my mostly text based site, widgets for my social media pages and a clean, fun, light feel for the site.

Target Market(s)

People looking to take charge of their own health, and who may need my coaching services to obtain optimal wellness.

Industry/Entity Type

Health

Coding

Coded - Design and coding required

Number of Pages Required

5+ page

Font styles to use
Script

Colors
33b8a4
33a6d7
ffffff

Requirements
Must have
• Must incorporate my logo design, as well as same/similar fonts and color scheme.
• I'd like it to stay as close to the current design as possible.
Nice to have
• Would love to incorporate a hover over menu (for example, when a user hovers over "About", they will see the submenu in a floating design.
Should not have
• No dark colors or masculine feel

```html
<!DOCTYPE html>
<html lang="en">
<head>
<meta charset="utf-8">
<title>Ridgeway Fern Lady</title>
<link href="https://fonts.googleapis.com/css2?family=Oswald:wght@400;500&family=Roboto:wght@400;500;700&display=swap" rel="stylesheet">
<style>
:root{
  --blue:#2f8fd8;
  --blue-btn:#3d94e0;
  --green:#86c150;
  --teal:#33b8a4;
  --ink:#333;
  --muted:#666;
  --page:#ececec;
  --card:#fff;
  --line:#e2e2e2;
  --footer-light:#f2f2f2;
  --footer-dark:#2b2b2b;
}
*{box-sizing:border-box;margin:0;padding:0}
html,body{width:1200px;height:2835px;overflow:hidden}
body{position:relative;background:var(--page);font-family:'Roboto',Arial,sans-serif;color:var(--ink)}
a{color:inherit;text-decoration:none}

/* header */
.site-header{position:absolute;left:0;top:0;width:1200px;height:110px;background:#fff}
.brand{position:absolute;left:106px;top:44px;font-size:24px;font-weight:500;color:var(--teal);letter-spacing:.5px}
.main-nav{position:absolute;left:403px;top:56px;display:flex;gap:0;font-size:15px;text-transform:uppercase;color:#333}
.main-nav a{position:absolute;white-space:nowrap}
.main-nav .active{color:var(--blue)}
.submenu{position:absolute;left:378px;top:110px;width:155px;height:134px;background:rgba(225,225,225,.93);z-index:5;padding:16px 0 0 25px;font-size:14px;line-height:27px;text-transform:uppercase;color:#444}

/* hero */
.hero{position:absolute;left:0;top:110px;width:1200px;height:538px;background:linear-gradient(100deg,#6b6460 0%,#9c918c 30%,#d8d2cf 55%,#7a5446 80%,#5a3b32 100%)}
.hero-title{position:absolute;left:121px;top:172px;font-family:'Oswald',Arial,sans-serif;font-weight:500;color:#fff;font-size:66px;line-height:1;text-transform:uppercase}
.hero-sub{position:absolute;left:121px;top:250px;font-family:'Oswald',Arial,sans-serif;color:#fff;font-size:36px;line-height:1;text-transform:uppercase}
.hero-arrow{position:absolute;top:223px;width:38px;height:38px}
.hero-arrow.prev{left:32px}.hero-arrow.next{left:1129px}

/* posts */
.post{position:absolute;left:104px;width:610px;height:421px;background:var(--card);border:1px solid #dcdcdc;box-shadow:0 1px 3px rgba(0,0,0,.08)}
.post-media{position:absolute;left:9px;top:9px;width:590px;height:204px}
.post-date{position:absolute;left:9px;top:9px;width:57px;height:62px;background:#111;color:#fff;text-align:center;font-size:12px;line-height:1.1;padding-top:6px}
.post-date b{display:block;font-size:22px;font-weight:400}
.post-date span{font-size:10px}
.post-title{position:absolute;left:20px;top:247px;font-size:14px;color:var(--blue);text-transform:uppercase}
.post-excerpt{position:absolute;left:20px;top:276px;width:570px;font-size:11.5px;line-height:19px;color:#333}
.post-meta{position:absolute;left:16px;top:345px;font-size:11.5px;color:#333}
.post-share{position:absolute;left:0;top:372px;width:608px;border-top:1px solid var(--line);height:48px}
.share{position:absolute;top:15px;display:flex;align-items:center;gap:4px;font-size:10px}
.share .btn{height:18px;padding:0 7px;border:1px solid #bbb;border-radius:3px;background:#f1f1f1;line-height:16px;color:#444;font-weight:700}
.share .btn.like{background:#4a68ab;color:#fff;border-color:#3e5a96}
.share .btn.plus{color:#c6403a}
.share .count{height:18px;min-width:20px;border:1px solid #ccc;line-height:16px;text-align:center;color:#555;background:#fff}

/* sidebar */
.widget{position:absolute;left:760px;width:338px;background:#fff;border:1px solid #dcdcdc;box-shadow:0 1px 3px rgba(0,0,0,.08)}
.search-box{top:705px;height:91px}
.search-input{position:absolute;left:17px;top:27px;width:194px;height:38px;background:#e6e6e6;font-size:11px;font-style:italic;color:#777;padding:14px 0 0 15px}
.search-btn{position:absolute;left:218px;top:27px;width:98px;height:36px;background:var(--blue-btn);color:#fff;font-size:13px;text-align:center;line-height:36px;border-radius:2px}
.popular{top:813px;height:570px}
.widget-heading{font-size:19px;color:var(--blue);text-transform:uppercase;padding:22px 0 0 27px}
.pop-item{position:absolute;left:25px;width:300px;height:80px}
.pop-thumb{position:absolute;left:0;top:2px;width:94px;height:66px;border:3px solid #fff;box-shadow:0 1px 4px rgba(0,0,0,.35)}
.pop-title{position:absolute;left:105px;top:0;font-size:12px;color:var(--blue)}
.pop-text{position:absolute;left:105px;top:18px;width:170px;font-size:10.5px;line-height:17px;color:#555}
.list-widget .bar{height:50px;background:var(--green);color:#fff;font-size:20px;text-transform:uppercase;padding:13px 0 0 36px}
.archives{top:1397px;height:389px}
.categories{top:1799px;height:352px}
.list-widget ul{list-style:none;padding:18px 0 0 36px}
.list-widget li{display:flex;align-items:center;gap:16px;font-size:15px;color:#333;height:40px}
.ad{top:2164px;height:293px}
.ad-inner{position:absolute;left:47px;top:19px;width:248px;height:248px;background:#eee;text-align:center}
.ad-head{font-family:'Oswald',Arial,sans-serif;font-size:17px;line-height:19px;color:#333;padding-top:10px;text-transform:uppercase}
.ad-head strong{font-weight:500}
.ad-covers{position:absolute;left:10px;top:72px;width:140px;height:100px;background:linear-gradient(90deg,#7d5a8a,#3d6aa8,#c84b4b,#4a8e8a)}
.ad-badge{position:absolute;left:152px;top:70px;width:90px;height:90px;border-radius:50%;background:#3a9ad6}
.ad-help{position:absolute;left:0;top:178px;width:248px;font-size:19px;font-style:italic;color:#333}
.ad-cta{position:absolute;left:52px;top:210px;width:134px;height:32px;background:#f28a1e;color:#fff;font-size:14px;font-weight:700;line-height:32px;border-radius:3px}

/* footer */
.footer-links{position:absolute;left:0;top:2510px;width:1200px;height:189px;background:var(--footer-light);border-top:1px solid #e0e0e0}
.footer-col{position:absolute;top:30px}
.footer-col h4{font-size:18px;font-weight:400;color:var(--blue);margin-bottom:16px}
.footer-col a{display:block;font-size:11.5px;line-height:24px;color:#333}
.footer-bottom{position:absolute;left:0;top:2699px;width:1200px;height:136px;background:var(--footer-dark);color:#eee}
.legal{position:absolute;left:104px;top:40px;font-size:12.5px;line-height:30px}
.social{position:absolute;left:860px;top:40px;display:flex;gap:16px}
.social span{width:44px;height:44px;border-radius:50%;border:2px solid #fff}
</style>
</head>
<body>

<header class="site-header">
  <a class="brand" href="#">Ridgeway Fern Lady</a>
  <nav class="main-nav">
    <a class="active" href="#" style="left:0">About Nora</a>
    <a href="#" style="left:120px">Articles</a>
    <a href="#" style="left:224px">Essential Oils</a>
    <a href="#" style="left:374px">21-Day Sweet Reset Coaching Services</a>
  </nav>
</header>
<div class="submenu"><div>Sub Menu 1</div><div>Sub Menu 2</div><div>Sub Menu 3</div><div>Sub Menu 4</div></div>

<section class="hero" role="img" aria-label="Woman in a white knit hat and scarf outdoors in a snowy scene">
  <h1 class="hero-title">Ridgeway Fern Lady</h1>
  <p class="hero-sub">Ipsum is simply dummy</p>
  <svg class="hero-arrow prev" viewBox="0 0 38 38"><circle cx="19" cy="19" r="19" fill="#fff"/><path d="M22 11l-8 8 8 8" fill="none" stroke="#222" stroke-width="3"/></svg>
  <svg class="hero-arrow next" viewBox="0 0 38 38"><circle cx="19" cy="19" r="19" fill="#fff"/><path d="M16 11l8 8-8 8" fill="none" stroke="#222" stroke-width="3"/></svg>
</section>

<!-- posts -->
<article class="post" style="top:705px">
  <div class="post-media" role="img" aria-label="Woman sitting on a rock by the sea" style="background:linear-gradient(180deg,#c9d9de 0%,#7aa5a6 55%,#a8a39a 100%)"></div>
  <div class="post-date">Dec<b>20</b><span>2015</span></div>
  <h2 class="post-title">Lifestyles of the tired and wired</h2>
  <p class="post-excerpt">Lorem Ipsum has been the industry's standard dummy text ever since the 1500s, when an unknown printer took a galley of type and scrambled it to make a type specimen book. It has survived not only</p>
  <p class="post-meta">This entry was posted in Hearthside on 11/01/2015.</p>
  <div class="post-share">
    <div class="share" style="left:314px"><span class="btn">Post</span><span class="count">0</span></div>
    <div class="share" style="left:420px"><span class="btn like">Like</span><span class="count">0</span></div>
    <div class="share" style="left:528px"><span class="btn plus">+1</span><span class="count">0</span></div>
  </div>
</article>

<article class="post" style="top:1147px">
  <div class="post-media" role="img" aria-label="Group of smiling young friends outdoors" style="background:linear-gradient(180deg,#bcd3e3 0%,#9a7c6a 55%,#4d5a6e 100%)"></div>
  <div class="post-date">Dec<b>20</b><span>2015</span></div>
  <h2 class="post-title">April Essential Living Education Series</h2>
  <p class="post-excerpt">Lorem Ipsum has been the industry's standard dummy text ever since the 1500s, when an unknown printer took a galley of type and scrambled it to make a type specimen book. It has survived not only</p>
  <p class="post-meta">This entry was posted in Hearthside on 11/01/2015.</p>
  <div class="post-share">
    <div class="share" style="left:314px"><span class="btn">Post</span><span class="count">0</span></div>
    <div class="share" style="left:420px"><span class="btn like">Like</span><span class="count">0</span></div>
    <div class="share" style="left:528px"><span class="btn plus">+1</span><span class="count">0</span></div>
  </div>
</article>

<article class="post" style="top:1593px">
  <div class="post-media" role="img" aria-label="Group of students standing outdoors under a blue sky" style="background:linear-gradient(180deg,#6f9fd6 0%,#b7cde6 40%,#7b6a5a 75%,#4e5b45 100%)"></div>
  <div class="post-date">Dec<b>20</b><span>2015</span></div>
  <h2 class="post-title">Module 3: A nice supplement to the program</h2>
  <p class="post-excerpt">Lorem Ipsum has been the industry's standard dummy text ever since the 1500s, when an unknown printer took a galley of type and scrambled it to make a type specimen book. It has survived not only</p>
  <p class="post-meta">This entry was posted in Hearthside and tagged defender, Trail Wagon on 06/01/2015.</p>
  <div class="post-share">
    <div class="share" style="left:314px"><span class="btn">Post</span><span class="count">0</span></div>
    <div class="share" style="left:420px"><span class="btn like">Like</span><span class="count">0</span></div>
    <div class="share" style="left:528px"><span class="btn plus">+1</span><span class="count">0</span></div>
  </div>
</article>

<article class="post" style="top:2035px">
  <div class="post-media" role="img" aria-label="Young woman in a library beside bookshelves" style="background:linear-gradient(90deg,#e4e0da 0%,#b08a72 35%,#6e4f3c 70%,#3f342d 100%)"></div>
  <div class="post-date">Dec<b>20</b><span>2015</span></div>
  <h2 class="post-title">Module 3: A nice supplement to the program</h2>
  <p class="post-excerpt">Lorem Ipsum has been the industry's standard dummy text ever since the 1500s, when an unknown printer took a galley of type and scrambled it to make a type specimen book. It has survived not only</p>
  <p class="post-meta">This entry was posted in Hearthside and tagged defender, Trail Wagon on 06/01/2015.</p>
  <div class="post-share">
    <div class="share" style="left:314px"><span class="btn">Post</span><span class="count">0</span></div>
    <div class="share" style="left:420px"><span class="btn like">Like</span><span class="count">0</span></div>
    <div class="share" style="left:528px"><span class="btn plus">+1</span><span class="count">0</span></div>
  </div>
</article>

<!-- sidebar -->
<aside class="widget search-box">
  <div class="search-input">Search</div>
  <div class="search-btn">Search</div>
</aside>

<aside class="widget popular">
  <h3 class="widget-heading">Popular Blogs</h3>
  <div class="pop-item" style="top:77px"><div class="pop-thumb" role="img" aria-label="Post thumbnail photo" style="background:#d9b9a6"></div><div class="pop-title">This is a sample Post 1</div><p class="pop-text">Lorem ipsum dolor sit amet, consectetuer adipiscing elit, sed diam nonummy nibh...</p></div>
  <div class="pop-item" style="top:177px"><div class="pop-thumb" role="img" aria-label="Post thumbnail photo" style="background:#8c97a8"></div><div class="pop-title">This is a sample Post 1</div><p class="pop-text">Lorem ipsum dolor sit amet, consectetuer adipiscing elit, sed diam nonummy nibh...</p></div>
  <div class="pop-item" style="top:277px"><div class="pop-thumb" role="img" aria-label="Post thumbnail photo" style="background:#a9b5c2"></div><div class="pop-title">This is a sample Post 1</div><p class="pop-text">Lorem ipsum dolor sit amet, consectetuer adipiscing elit, sed diam nonummy nibh...</p></div>
  <div class="pop-item" style="top:367px"><div class="pop-thumb" role="img" aria-label="Post thumbnail photo" style="background:#6a4f48"></div><div class="pop-title">This is a sample Post 1</div><p class="pop-text">Lorem ipsum dolor sit amet, consectetuer adipiscing elit, sed diam nonummy nibh...</p></div>
  <div class="pop-item" style="top:467px"><div class="pop-thumb" role="img" aria-label="Post thumbnail photo" style="background:#c9a27e"></div><div class="pop-title">This is a sample Post 1</div><p class="pop-text">Lorem ipsum dolor sit amet, consectetuer adipiscing elit, sed diam nonummy nibh...</p></div>
</aside>

<svg width="0" height="0" style="position:absolute"><defs><symbol id="chev" viewBox="0 0 14 12"><path d="M1 1l5 5-5 5M7 1l5 5-5 5" fill="none" stroke="#2f8fd8" stroke-width="1.8"/></symbol></defs></svg>

<aside class="widget list-widget archives">
  <div class="bar">Archives</div>
  <ul>
    <li><svg width="14" height="12"><use href="#chev"/></svg>April 2015</li>
    <li><svg width="14" height="12"><use href="#chev"/></svg>March 2015</li>
    <li><svg width="14" height="12"><use href="#chev"/></svg>February 2015</li>
    <li><svg width="14" height="12"><use href="#chev"/></svg>January 2015</li>
    <li><svg width="14" height="12"><use href="#chev"/></svg>September 2014</li>
    <li><svg width="14" height="12"><use href="#chev"/></svg>June 2014</li>
    <li><svg width="14" height="12"><use href="#chev"/></svg>May 2014</li>
    <li><svg width="14" height="12"><use href="#chev"/></svg>April 2014</li>
  </ul>
</aside>

<aside class="widget list-widget categories">
  <div class="bar">Categories</div>
  <ul>
    <li><svg width="14" height="12"><use href="#chev"/></svg>21 Day Sweet Reset</li>
    <li><svg width="14" height="12"><use href="#chev"/></svg>Adrenal Fatigue</li>
    <li><svg width="14" height="12"><use href="#chev"/></svg>Articles</li>
    <li><svg width="14" height="12"><use href="#chev"/></svg>DIY</li>
    <li><svg width="14" height="12"><use href="#chev"/></svg>Essential Oils</li>
    <li><svg width="14" height="12"><use href="#chev"/></svg>Real Food</li>
    <li><svg width="14" height="12"><use href="#chev"/></svg>Uncategorized</li>
  </ul>
</aside>

<aside class="widget ad">
  <div class="ad-inner">
    <p class="ad-head">Need <strong>extra support</strong><br>to <strong>rock</strong> your<br><strong>21-Day Sweet Reset?</strong></p>
    <div class="ad-covers" role="img" aria-label="Stack of program guide books"></div>
    <div class="ad-badge"></div>
    <p class="ad-help">I'm here to help</p>
    <div class="ad-cta">TELL ME MORE!</div>
  </div>
</aside>

<!-- footer -->
<footer>
  <div class="footer-links">
    <div class="footer-col" style="left:123px"><h4>How We Help</h4><a href="#">Lead Generation</a><a href="#">Tactics Management</a><a href="#">Start-Up Website</a><a href="#">Website Facelifts</a></div>
    <div class="footer-col" style="left:401px"><h4>Services</h4><a href="#">Social Media Coaching</a><a href="#">Website Analysis</a><a href="#">Nimbus Website Design</a><a href="#">Newsletters</a></div>
    <div class="footer-col" style="left:680px"><h4>Results</h4><a href="#">Testimonials</a><a href="#">B2B Companies</a><a href="#">Contractors &amp; Construction</a><a href="#">Manufacturing</a></div>
    <div class="footer-col" style="left:937px"><h4>Support</h4><a href="#">Why Choose Brightpath</a><a href="#">Our Culture</a><a href="#">Our Team</a><a href="#">Sitemap</a></div>
  </div>
  <div class="footer-bottom">
    <div class="legal">Privacy Policy | Terms of Use | About Us | Sitemap<br>Copyright © 2015 All rights reserved.</div>
    <div class="social" aria-label="Social media links"><span></span><span></span><span></span><span></span></div>
  </div>
</footer>

</body>
</html>
```